Boutique custom software development company needs new business card

Our nearly 20 year old custom software development company would like to better include the fact that we are now providing Bitcoin services. These new services are B2B include education (how to acquire and securely hold Bitcoin) and integrating Bitcoin payments into existing ecommerce sites or other existing systems. Please keep the card clean and simple. Attached is our current design and some other files. vextorial.com

Target Market(s)

businesses owners interested in long term relationship

Industry/Entity Type

Custom software development and Bitcoin

Contact Information for Business Card

Dale Parker, dale@vextorial.com, vextorial.com, (888) 555-VXTRL

Font styles to use
Other font styles liked:
• monospace

Requirements
Must have
• double-sided
Nice to have
• clean and simple
Should not have
• physical address

```html
<!DOCTYPE html>
<html lang="en">
<head>
<meta charset="utf-8">
<title>Vextorial Business Card</title>
<link href="https://fonts.googleapis.com/css2?family=Source+Sans+3:wght@400;600;700&display=swap" rel="stylesheet">
<style>
  :root {
    --brand-blue: #3d72b9;
    --brand-orange: #f07a22;
    --ink: #444444;
    --paper: #ffffff;
    --backdrop: #232323;
  }
  * { box-sizing: border-box; margin: 0; padding: 0; }
  html, body {
    width: 1200px;
    height: 1200px;
    overflow: hidden;
    background: var(--backdrop);
    font-family: "Source Sans 3", "Source Sans Pro", sans-serif;
  }
  .card {
    position: absolute;
    left: 250px;
    width: 700px;
    height: 400px;
    border-radius: 27px;
    overflow: hidden;
  }
  .card-front { top: 170px; background: var(--paper); }
  .card-back { top: 631px; background: var(--brand-blue); }

  .brand-mark {
    position: absolute;
    right: 54px;
    top: 92px;
    display: flex;
    align-items: center;
    gap: 10px;
  }
  .brand-square {
    width: 26px;
    height: 26px;
    background: var(--brand-orange);
  }
  .brand-name {
    font-weight: 700;
    font-size: 30px;
    letter-spacing: 1px;
    color: var(--brand-blue);
    line-height: 1;
  }

  .person-name {
    position: absolute;
    left: 48px;
    top: 225px;
    font-size: 29px;
    font-weight: 700;
    letter-spacing: 1.2px;
    color: var(--brand-blue);
    line-height: 1;
  }
  .person-title {
    position: absolute;
    left: 48px;
    top: 256px;
    font-size: 17.5px;
    color: var(--brand-orange);
    line-height: 1;
  }
  .divider {
    position: absolute;
    left: 47px;
    top: 288px;
    width: 600px;
    height: 1.5px;
    background: var(--brand-blue);
  }
  .contact-list {
    position: absolute;
    left: 47px;
    top: 307px;
    list-style: none;
  }
  .contact-item {
    display: flex;
    align-items: center;
    gap: 10px;
    color: var(--ink);
    line-height: 1;
  }
  .contact-item + .contact-item { margin-top: 9px; }
  .contact-phone { font-size: 19px; }
  .contact-email { font-size: 16.5px; }
  .contact-icon { width: 14px; height: 14px; fill: var(--brand-blue); flex: none; }

  .footer-bands { position: absolute; left: 0; bottom: 0; width: 700px; height: 34px; }
  .site-url {
    position: absolute;
    right: 20px;
    bottom: 7px;
    font-size: 15px;
    letter-spacing: 3.4px;
    color: var(--paper);
    line-height: 1;
  }

  .back-lockup {
    position: absolute;
    left: 0;
    right: 0;
    top: 128px;
    text-align: center;
    color: var(--paper);
  }
  .back-name {
    font-weight: 700;
    font-size: 86px;
    letter-spacing: 1px;
    line-height: 1;
  }
  .back-tagline {
    margin-top: 10px;
    font-size: 31px;
    letter-spacing: -1.2px;
    line-height: 1;
  }
  .back-services {
    margin-top: 14px;
    font-size: 19px;
    letter-spacing: 0.3px;
    line-height: 1;
    color: var(--paper);
  }
  .back-services .accent { color: var(--brand-orange); font-weight: 600; }
</style>
</head>
<body>
  <section class="card card-front" aria-label="Business card front">
    <div class="brand-mark">
      <span class="brand-square"></span>
      <span class="brand-name">VEXTORIAL</span>
    </div>

    <h1 class="person-name">DALE PARKER</h1>
    <p class="person-title">Founding Partner</p>
    <div class="divider"></div>

    <ul class="contact-list">
      <li class="contact-item contact-phone">
        <svg class="contact-icon" viewBox="0 0 24 24" aria-hidden="true">
          <path d="M6.6 10.8a15.2 15.2 0 0 0 6.6 6.6l2.2-2.2a1 1 0 0 1 1-.25 11.4 11.4 0 0 0 3.6.57 1 1 0 0 1 1 1V20a1 1 0 0 1-1 1A17 17 0 0 1 3 4a1 1 0 0 1 1-1h3.5a1 1 0 0 1 1 1c0 1.25.2 2.45.57 3.6a1 1 0 0 1-.25 1z"/>
        </svg>
        (888) 555-VXTRL
      </li>
      <li class="contact-item contact-email">
        <svg class="contact-icon" viewBox="0 0 24 24" aria-hidden="true">
          <path d="M2 5h20v14H2z M3.5 6.5 12 13l8.5-6.5" fill="none" stroke="#3d72b9" stroke-width="2"/>
        </svg>
        dale@vextorial.com
      </li>
    </ul>

    <svg class="footer-bands" viewBox="0 0 700 34" aria-hidden="true">
      <polygon points="0,23 459,23 448,34 0,34" fill="#f07a22"/>
      <polygon points="487,0 700,0 700,34 455,34" fill="#3d72b9"/>
    </svg>
    <span class="site-url">WWW.VEXTORIAL.COM</span>
  </section>

  <section class="card card-back" aria-label="Business card back">
    <div class="back-lockup">
      <div class="back-name">VEXTORIAL</div>
      <p class="back-tagline">developer of custom applications</p>
      <p class="back-services"><span class="accent">Bitcoin services:</span> education &amp; payment integration</p>
    </div>
  </section>
</body>
</html>
```